Jolly Paws Business Card Update

I have a business card which I love. I want to keep the same logo, colours, font and style. I want to upgrade the scripting and remove some elements and add others.
On the front side under Services - remove the existing wording and insert - Providing individual coaching strategies to create happy, healthy and social canine companions
Under Denise Carvell amend the current wording to read: Qualified in Dog Behavioural Training, Natural Animal Healthcare and Animal Health Science
On the reverse side to remove the web address.

```html
<!DOCTYPE html>
<html lang="en">
<head>
<meta charset="utf-8">
<title>Jolly Paws Business Card</title>
<link rel="stylesheet" href="https://fonts.googleapis.com/css2?family=Open+Sans:ital,wght@0,400;0,600;0,700;1,400&family=Ubuntu:wght@500&family=Arimo:wght@400;700&display=swap">
<style>
  :root {
    --bg: #2b2b2d;
    --blue-deep: #1f3f92;
    --blue-bright: #0a8ccb;
    --red-dark: #6a1616;
    --red: #c81d22;
    --navy: #26307a;
    --paper: #f1f1f1;
    --white: #ffffff;
    --pill: #eef0f4;
  }
  * { box-sizing: border-box; margin: 0; padding: 0; }
  html, body { width: 1200px; height: 1138px; overflow: hidden; background: var(--bg); }
  body { position: relative; font-family: "Open Sans", sans-serif; }

  .card {
    position: absolute;
    border-radius: 14px;
    overflow: hidden;
    box-shadow: 0 6px 14px rgba(0,0,0,.45);
  }

  /* Front */
  .card-front {
    left: 274px; top: 186px; width: 623px; height: 376px;
    background: linear-gradient(200deg, var(--blue-bright) 0%, #1a62b5 45%, var(--blue-deep) 100%);
  }
  .front-mark {
    position: absolute; left: 235px; top: 35px; width: 150px; height: 150px;
    border-radius: 50%; background: var(--red);
  }
  .front-name {
    position: absolute; left: 0; right: 0; top: 192px; text-align: center;
    font-weight: 700; font-size: 38px; line-height: 48px; color: var(--white);
    letter-spacing: 1px;
  }
  .front-tagline {
    position: absolute; left: 0; right: 0; top: 236px; text-align: center;
    font-size: 21px; line-height: 26px; color: var(--white);
  }
  .front-band {
    position: absolute; left: 0; right: 0; top: 302px; bottom: 0;
    background: linear-gradient(90deg, var(--red-dark) 0%, var(--red) 55%, var(--red-dark) 100%);
  }
  .services-pill {
    position: absolute; left: 218px; top: 288px; width: 186px; height: 28px;
    border-radius: 14px; background: var(--pill); border: 2px solid #1c4fa0;
    text-align: center; font-weight: 700; font-size: 17px; line-height: 24px;
    letter-spacing: 2.5px; color: var(--navy);
  }
  .front-services {
    position: absolute; left: 0; right: 0; top: 318px; text-align: center;
    font-size: 16px; line-height: 22px; color: #f3e6e6;
  }

  /* Back */
  .card-back {
    left: 276px; top: 608px; width: 618px; height: 374px;
    background: linear-gradient(180deg, #f7f7f7, var(--paper));
  }
  .back-wave { position: absolute; left: 0; top: 0; }
  .person-name {
    position: absolute; left: 41px; top: 46px;
    font-family: "Ubuntu", sans-serif; font-weight: 500; font-size: 26px; line-height: 32px;
    color: var(--navy);
  }
  .qualifications {
    position: absolute; left: 41px; top: 80px;
    font-style: italic; font-size: 16px; line-height: 21px; color: var(--navy);
  }
  .contact-list { position: absolute; left: 41px; top: 169px; list-style: none; }
  .contact-list li {
    display: flex; align-items: center; height: 23px;
    font-size: 16px; color: var(--navy);
  }
  .contact-list svg { width: 14px; height: 14px; margin-right: 15px; flex: none; }
  .back-mark {
    position: absolute; left: 439px; top: 41px; width: 134px; height: 134px;
    border-radius: 50%; background: var(--red);
  }
  .back-services {
    position: absolute; right: 25px; top: 276px; text-align: right;
    font-family: "Arimo", sans-serif; font-size: 16px; line-height: 19px; color: #f4e8e8;
  }
  .back-services strong { font-weight: 700; display: block; }
</style>
</head>
<body>

<section class="card card-front" aria-label="Card front">
  <div class="front-mark" aria-hidden="true"></div>
  <h1 class="front-name">JOLLY PAWS</h1>
  <p class="front-tagline">HAPPY DOGS, HAPPY OWNERS</p>
  <div class="front-band"></div>
  <div class="services-pill">SERVICES</div>
  <p class="front-services">Providing individual coaching strategies to create happy,<br>healthy and social canine companions</p>
</section>

<section class="card card-back" aria-label="Card back">
  <svg class="back-wave" width="618" height="374" viewBox="0 0 618 374" aria-hidden="true">
    <defs>
      <linearGradient id="redBand" x1="0" x2="1" y1="0" y2="0">
        <stop offset="0" stop-color="#6a1616"/>
        <stop offset="0.55" stop-color="#c81d22"/>
        <stop offset="1" stop-color="#7a1a1a"/>
      </linearGradient>
      <linearGradient id="blueBand" x1="0" x2="1" y1="0" y2="0">
        <stop offset="0" stop-color="#1f3f92"/>
        <stop offset="1" stop-color="#1d6fc0"/>
      </linearGradient>
    </defs>
    <path d="M0 258 C90 310 200 330 300 290 C400 250 480 190 618 200 L618 230 C480 214 400 262 300 306 C200 346 90 334 0 290 Z" fill="url(#blueBand)"/>
    <path d="M0 302 C90 350 200 362 300 318 C400 272 480 216 618 240 L618 374 L0 374 Z" fill="url(#redBand)"/>
  </svg>

  <h2 class="person-name">Denise Carvell</h2>
  <p class="qualifications">Qualified in Dog Behavioural Training,<br>Natural Animal Healthcare and<br>Animal Health Science</p>

  <ul class="contact-list">
    <li>
      <svg viewBox="0 0 14 14" aria-hidden="true"><rect x="3.5" y="0.5" width="7" height="13" rx="1.2" fill="none" stroke="#c81d22" stroke-width="1.4"/><rect x="5" y="2.5" width="4" height="4" fill="#c81d22"/></svg>
      0400 271 536
    </li>
    <li>
      <svg viewBox="0 0 14 14" aria-hidden="true"><rect x="0.5" y="3" width="13" height="9" fill="#c81d22"/><path d="M0.5 3 L7 8 L13.5 3" fill="none" stroke="#fff" stroke-width="1"/></svg>
      jollypaws1@mailbox.com
    </li>
  </ul>

  <div class="back-mark" aria-hidden="true"></div>

  <p class="back-services"><strong>SERVICES:</strong>Providing Individual Coaching<br>Strategies to Create Happy,<br>Healthy &amp; Social Canine Companions</p>
</section>

</body>
</html>
```